Board to put on a meditation centre - Lantern Grove

I need a board design for a new meditation centre based in Oslo which offers free courses in meditation and self-empowerment. The size of the board is width 374cm x height 104cm.  The name of the meditation centre together with subtitles should be on the board but also some elegant decoration that matches the theme (lantern grove/meditation).
Here is the website of the meditation centre to give you a feeling of it: https://kvitfjellsenteret.no/
Good if you can use a blue color close to this one: rgb(37, 180, 193) as well as some brown/golden color (similar to the palette on the website).
On the board it should say:
Kveldens lund (in big letters, the rest is subtitles)
Meditasjon & Spirituell visdom
Kurs - Retreat - Dialog
kvitfjellsenteret.no
The design should be very elegant and beautiful and the feeling should be of "A Lantern Grove". A logo is here attached and should be used but I need to get a better quality version of it, will upload that as soon as possible.

```html
<!DOCTYPE html>
<html lang="no">
<head>
<meta charset="utf-8">
<title>Kveldens lund – skilt</title>
<link href="https://fonts.googleapis.com/css2?family=Source+Sans+3:wght@300;400;600;700;900&display=swap" rel="stylesheet">
<style>
  :root {
    --page: #ffffff;
    --sky-top: #ffffff;
    --sky-bottom: #a6f2fb;
    --blue: #0a7dcd;
    --brown: #6f5a50;
    --taupe: #8b7d77;
    --icon: #2b86d3;
    --brand: #9a2637;
    --photo-a: #dfeff2;
    --photo-b: #8fb7bf;
  }
  * { box-sizing: border-box; margin: 0; padding: 0; }
  html, body { width: 1200px; height: 1182px; overflow: hidden; background: var(--page); }
  body { font-family: "Source Sans 3", "Source Sans Pro", sans-serif; position: relative; }

  .board {
    position: absolute; left: 40px; top: 435px; width: 1120px; height: 311px;
    background: linear-gradient(180deg, var(--sky-top) 0%, var(--sky-bottom) 100%);
    box-shadow: 0 2px 10px rgba(0,0,0,0.18);
    overflow: hidden;
  }
  .brand {
    position: absolute; left: 43px; top: 31px;
    display: flex; align-items: center; gap: 9px;
  }
  .brand-dot { width: 28px; height: 28px; border-radius: 50%; background: var(--brand); }
  .brand-name {
    font-weight: 400; font-size: 17px; letter-spacing: 2.5px; color: var(--brand);
    text-transform: uppercase; line-height: 1;
  }
  .title {
    position: absolute; left: 44px; top: 75px;
    font-size: 72px; font-weight: 900; line-height: 1; letter-spacing: 0.5px;
    white-space: nowrap;
  }
  .title .lead { color: var(--blue); }
  .title .rest { color: var(--brown); }
  .subtitle {
    position: absolute; left: 44px; top: 146px;
    font-size: 44px; font-weight: 400; line-height: 1; color: var(--taupe); letter-spacing: 0.3px;
    white-space: nowrap;
  }
  .offers {
    position: absolute; left: 46px; top: 201px;
    display: flex; gap: 30px; list-style: none;
  }
  .offers li {
    display: flex; align-items: center; gap: 8px;
    font-size: 32px; font-weight: 600; color: var(--brown); line-height: 1;
  }
  .offers svg { width: 26px; height: 26px; }
  .web {
    position: absolute; left: 46px; top: 259px;
    display: flex; align-items: center; gap: 12px;
    font-size: 21px; font-weight: 700; color: var(--blue); line-height: 1;
  }
  .web svg { width: 22px; height: 22px; }
  .base-band {
    position: absolute; left: 0; bottom: 0; width: 100%; height: 21px; background: var(--blue);
  }
  .hero-visual {
    position: absolute; left: 838px; top: 5px; width: 280px; height: 306px;
    background: radial-gradient(circle at 50% 42%, var(--photo-a) 0%, var(--photo-b) 62%, rgba(143,183,191,0) 72%);
  }
</style>
</head>
<body>
  <section class="board">
    <div class="brand">
      <span class="brand-dot"></span>
      <span class="brand-name">Lysglott Fellesskap</span>
    </div>

    <h1 class="title"><span class="lead">KVELDENS</span> <span class="rest">LUND</span></h1>
    <p class="subtitle">MEDITASJON &amp; SPIRITUELL VISDOM</p>

    <ul class="offers">
      <li>
        <svg viewBox="0 0 26 26" fill="none" stroke="var(--icon)" stroke-width="1.6">
          <rect x="3" y="4" width="20" height="14"/><line x1="2" y1="4" x2="24" y2="4"/>
          <rect x="6" y="8" width="6" height="6"/><line x1="14" y1="9" x2="20" y2="9"/><line x1="14" y1="13" x2="20" y2="13"/>
          <line x1="13" y1="18" x2="13" y2="23"/>
        </svg>Kurs
      </li>
      <li>
        <svg viewBox="0 0 26 26" fill="none" stroke="var(--icon)" stroke-width="1.6">
          <path d="M13 5c3 3 3 9 0 14c-3-5-3-11 0-14z"/><path d="M4 10c4 0 8 4 9 9c-5 0-9-4-9-9z"/><path d="M22 10c-4 0-8 4-9 9c5 0 9-4 9-9z"/>
        </svg>Retreat
      </li>
      <li>
        <svg viewBox="0 0 26 26" fill="none" stroke="var(--icon)" stroke-width="1.6">
          <path d="M2 3h15v10H8l-4 3v-3H2z"/><path d="M10 15v-2M19 8h5v11h-2v3l-4-3h-8v-4"/>
          <line x1="5" y1="7" x2="14" y2="7"/><line x1="5" y1="10" x2="12" y2="10"/>
        </svg>Dialog
      </li>
    </ul>

    <div class="web">
      <svg viewBox="0 0 22 22" fill="none" stroke="var(--blue)" stroke-width="1.5">
        <circle cx="11" cy="11" r="10"/><circle cx="11" cy="11" r="6"/><line x1="5" y1="11" x2="17" y2="11"/><path d="M11 5c-2 3-2 9 0 12M11 5c2 3 2 9 0 12"/>
      </svg>
      <span>www.lundlyssenteret-demo.no</span>
    </div>

    <div class="hero-visual" role="img" aria-label="Photo of a woman meditating cross-legged with palms joined, in front of a circular ornamental pattern"></div>

    <div class="base-band"></div>
  </section>
</body>
</html>
```